Dancing Emoji Lady but make it silhouette

We need a main image for the front of a hard wine seltzer. The best emoji that would describe this brand is the dancing lady in red dress emoji. We want to re-create the essence of this emoji in a silhouette (like an outline) so it's our own design, but it captures the fun and flirtatiousness of that emoji. We have three flavors - peach (peach color), fruit punch (red/purple color), and citrus (orange color) - so the only color should be the outline of her swooshing dress.

I'm attaching an image of the emoji I wish to emulate, and then some examples of what I mean by "silhouette" - I know the attached examples are not of a woman dancing, but it's the line/style that I want to emulate here to make a silhouette of the dancer emoji.

```html
<!DOCTYPE html>
<html lang="en">
<head>
<meta charset="utf-8">
<title>Lumera Peach Bellini – Can Label</title>
<link rel="stylesheet" href="https://fonts.googleapis.com/css2?family=Fraunces:opsz,wght@9..144,600;9..144,700&family=Oswald:wght@400;500&family=Antonio:wght@400&family=Sriracha&display=swap">
<style>
  :root {
    --stage: #e8e8e8;
    --label: #ffffff;
    --navy: #2c3150;
    --peach: #f29e88;
    --peach-soft: #fbdcd2;
    --badge: #f8cfc3;
    --badge-text: #f0907a;
    --dress: #a8232f;
    --dress-light: #d7545e;
  }
  * { margin: 0; padding: 0; box-sizing: border-box; }
  html, body { width: 1200px; height: 739px; overflow: hidden; background: var(--stage); }
  .stage { position: relative; width: 1200px; height: 739px; }
  .label {
    position: absolute; left: 450px; top: 126px;
    width: 301px; height: 485px; background: var(--label);
    text-align: center;
  }
  .claims-band {
    position: absolute; left: 0; top: 31px; width: 100%; height: 14px;
    background: var(--peach-soft);
    display: flex; align-items: center; justify-content: space-around;
    padding: 0 10px;
    font-family: "Oswald", sans-serif; font-weight: 500; font-size: 8.5px;
    letter-spacing: 0.4px; color: var(--peach);
  }
  .claims-band .dot { width: 2px; height: 2px; border-radius: 50%; background: #fff; }
  .brand-mark {
    position: absolute; left: 50%; top: 56px; transform: translateX(-50%);
    width: 22px; height: 22px; border-radius: 50%; background: var(--navy);
  }
  .brand-name {
    position: absolute; left: 0; top: 78px; width: 100%;
    font-family: "Fraunces", serif; font-weight: 700; font-size: 52px;
    line-height: 1; color: var(--navy); letter-spacing: -0.5px;
  }
  .tagline {
    position: absolute; left: 0; top: 129px; width: 100%;
    font-family: "Sriracha", cursive; font-size: 17px; line-height: 1;
    color: var(--peach); letter-spacing: 2px;
  }
  .dancer-art {
    position: absolute; left: 79px; top: 157px; width: 139px; height: 182px;
    border-radius: 46% 46% 40% 40%;
    background: radial-gradient(ellipse at 55% 55%, var(--dress-light) 0%, var(--dress) 70%, rgba(168,35,47,0.15) 100%);
  }
  .flavor {
    position: absolute; left: 0; top: 342px; width: 100%;
    font-family: "Antonio", sans-serif; font-weight: 400; font-size: 28px;
    line-height: 1.1; color: var(--peach); letter-spacing: 0.5px;
  }
  .product-type {
    position: absolute; left: 0; top: 376px; width: 100%;
    font-family: "Fraunces", serif; font-weight: 600; font-size: 12.5px;
    color: var(--navy);
  }
  .badges {
    position: absolute; left: 0; top: 401px; width: 100%;
    display: flex; justify-content: center; gap: 10px;
  }
  .badges .badge { width: 28px; height: 28px; display: block; }
  .badge circle { fill: var(--badge); }
  .badge text {
    font-family: "Oswald", sans-serif; font-weight: 500; font-size: 5.6px;
    fill: var(--badge-text); letter-spacing: 0.3px;
  }
  .volume {
    position: absolute; left: 0; top: 436px; width: 100%;
    font-family: "Oswald", sans-serif; font-weight: 500; font-size: 8.5px;
    color: var(--navy); letter-spacing: 0.3px;
  }
</style>
</head>
<body>
<main class="stage">
  <section class="label">
    <div class="claims-band">
      <span class="dot"></span><span>4G SUGAR</span><span class="dot"></span>
      <span>GLUTEN-FREE</span><span class="dot"></span>
      <span>120 CALORIES</span><span class="dot"></span>
      <span>WOMEN-OWNED</span><span class="dot"></span>
    </div>
    <span class="brand-mark"></span>
    <h1 class="brand-name">Lumera</h1>
    <p class="tagline">mi vino</p>
    <div class="dancer-art" role="img" aria-label="Line-art illustration of a woman dancing in a swirling red dress, raising a glass of wine"></div>
    <h2 class="flavor">PEACH BELLINI</h2>
    <p class="product-type">Hard Wine Seltzer</p>
    <div class="badges">
      <svg class="badge" viewBox="0 0 28 28" aria-label="Organic grapes">
        <defs>
          <path id="arc-top" d="M5,14 A9,9 0 0 1 23,14"/>
          <path id="arc-bottom" d="M4.5,14 A9.5,9.5 0 0 0 23.5,14"/>
        </defs>
        <circle cx="14" cy="14" r="14"/>
        <text text-anchor="middle"><textPath href="#arc-top" startOffset="50%">ORGANIC</textPath></text>
        <text text-anchor="middle" dy="4.5"><textPath href="#arc-bottom" startOffset="50%">GRAPES</textPath></text>
      </svg>
      <svg class="badge" viewBox="0 0 28 28" aria-label="Made in CA">
        <circle cx="14" cy="14" r="14"/>
        <text text-anchor="middle"><textPath href="#arc-top" startOffset="50%">MADE IN</textPath></text>
        <text x="14" y="22" text-anchor="middle">CA</text>
      </svg>
      <svg class="badge" viewBox="0 0 28 28" aria-label="Women operated">
        <circle cx="14" cy="14" r="14"/>
        <text text-anchor="middle"><textPath href="#arc-top" startOffset="50%">WOMEN</textPath></text>
        <text text-anchor="middle" dy="4.5"><textPath href="#arc-bottom" startOffset="50%">OPERATED</textPath></text>
      </svg>
    </div>
    <p class="volume">6% ABV &nbsp;|&nbsp; 250 mL</p>
  </section>
</main>
</body>
</html>
```